Van Signage Wrapping

Hi there, my name is Liam; I have a business called "Kvorin" servicing the Electrical, Security & AV (audio visual) industry. I currently have 2 X Vans working in Australia; I am looking to design a the graphics & lay out for the 2 X vans to be identical wrapped.
Should you wish to see the Van appearance (silver)
http://www.halvane.com.au/cars/merlotvan/colours
http://www.halvane.com.au/cars/merlotvan/home

Dimensions of the side panels are:
from the revision mirror to the tail 3.6meters
from the bottom if plastic to the top 1.35meters

Some of the words that describe our services are:
Commercial, Domestic, Automation, Networking, Data, Access Control, Alarms, CCTV, Audio Visual, Surround Sound, Home Cinema.
Allot of our work is taking these various technologies & linking them together for the user
Updates

Hi there, I have added a couple of thoughts in the 'nice to have' area of the brief I am very interested to see how you guys go, thank you for your designs so farĀ 

Target Market(s)

Builders, Developers, Home Owners, Buissness Owners

Industry/Entity Type

Plastic

Requirements
Must have
• The Logo "Kvorin" which is attached to the project
(m)0417 265 391
(e)sales@kvorin.com.au

I would like the side Logo on the van to run diagonal & hopefully take most of the advertising space over the sliding door & rear panel

REC No: 48302
Nice to have
• I have spent a little extra money on the Vans with more to come and I believe they look sharp & clean with the view to target well to do clients & larger projects, it would be great to keep the vans looking professional & clean. I like blue, white, black, lime-pale green against the silver colour but open to surjection.
In my head I imagined the Kvorin logo running on the largest side panels on the diagonal with the Electrical, Security, AV also running the length underneath the logo. With some of the words mentioned above that describe our services in various shades randomly placed horizontally in the back ground linked together with a sort of printed circuit board pattern. Again I am very open to ideas so please feel free to get creative. You can see one image I have uploaded a picture of a Ute with some words that are randomly placed & similar to the shade I am thinking of, I also like the Lime/Pale Green on the Ute if you can make it work
Measurements of Van Panels are attached

```html
<!DOCTYPE html>
<html lang="en">
<head>
<meta charset="utf-8">
<title>Kvorin – Van Side Panel Wrap</title>
<link rel="stylesheet" href="https://fonts.googleapis.com/css2?family=Barlow+Condensed:wght@600;700&family=Cormorant+Garamond:wght@500&display=swap">
<style>
  :root {
    --paper: #ffffff;
    --ink: #1a1a1a;
    --service-grey: #c6c6c6;
    --service-grey-light: #d0d0d0;
    --lime: #8dc63f;
    --guide: #cfcfcf;
    --guide-text: #555555;
  }
  html, body {
    margin: 0;
    padding: 0;
    width: 1200px;
    height: 467px;
    overflow: hidden;
    background: var(--paper);
  }
  .wrap-artboard { display: block; width: 1200px; height: 467px; }
  .dimension-line { stroke: var(--guide); stroke-width: 1; fill: none; }
  .dimension-label {
    font-family: "Barlow Condensed", Arial, sans-serif;
    font-weight: 600; font-size: 13px; fill: var(--guide-text);
  }
  .panel-outline { fill: var(--paper); stroke: #e2e2e2; stroke-width: 1; }
  .service-word {
    font-family: "Barlow Condensed", Arial, sans-serif;
    font-weight: 700; fill: var(--service-grey); letter-spacing: 0.5px;
  }
  .service-word--minor { font-weight: 600; fill: var(--service-grey-light); letter-spacing: 0; }
  .service-icon { fill: var(--lime); }
  .service-icon-glyph { fill: none; stroke: #ffffff; stroke-width: 1.6; }
  .brand-name {
    font-family: "Cormorant Garamond", "Times New Roman", serif;
    font-weight: 500; font-size: 150px; fill: var(--ink); letter-spacing: 2px;
  }
  .brand-tagline {
    font-family: "Cormorant Garamond", "Times New Roman", serif;
    font-weight: 500; font-size: 24px; fill: var(--ink);
    font-variant: small-caps; letter-spacing: 1.5px;
  }
  .contact-detail {
    font-family: "Barlow Condensed", Arial, sans-serif;
    font-weight: 700; font-size: 27px; fill: var(--ink);
  }
  .contact-icon { fill: none; stroke: var(--lime); stroke-width: 2.4; }
  .contact-icon--solid { fill: var(--lime); }
</style>
</head>
<body>
<svg class="wrap-artboard" viewBox="0 0 1200 467" xmlns="http://www.w3.org/2000/svg">
  <defs>
    <clipPath id="panel-clip"><rect x="2" y="33" width="1168" height="399"/></clipPath>
    <symbol id="icon-tile" viewBox="0 0 30 30">
      <rect class="service-icon" x="0" y="0" width="30" height="30" rx="4"/>
      <rect class="service-icon-glyph" x="7" y="8" width="16" height="14" rx="2"/>
      <circle class="service-icon-glyph" cx="15" cy="15" r="3"/>
    </symbol>
  </defs>

  <g class="measurements">
    <line class="dimension-line" x1="2" y1="8" x2="1170" y2="8"/>
    <line class="dimension-line" x1="2" y1="2" x2="2" y2="14"/>
    <line class="dimension-line" x1="484" y1="2" x2="484" y2="14"/>
    <line class="dimension-line" x1="812" y1="2" x2="812" y2="14"/>
    <line class="dimension-line" x1="1170" y1="2" x2="1170" y2="14"/>
    <rect x="212" y="0" width="72" height="14" fill="var(--paper)"/>
    <text class="dimension-label" x="248" y="10" text-anchor="middle">1750mm</text>
    <rect x="612" y="0" width="72" height="14" fill="var(--paper)"/>
    <text class="dimension-label" x="648" y="10" text-anchor="middle">1200mm</text>
    <rect x="950" y="0" width="72" height="14" fill="var(--paper)"/>
    <text class="dimension-label" x="986" y="10" text-anchor="middle">1300mm</text>

    <line class="dimension-line" x1="2" y1="460" x2="1170" y2="460"/>
    <rect x="562" y="452" width="76" height="15" fill="var(--paper)"/>
    <text class="dimension-label" x="600" y="464" text-anchor="middle">4250mm</text>

    <line class="dimension-line" x1="1190" y1="33" x2="1190" y2="432"/>
    <rect x="1182" y="205" width="16" height="70" fill="var(--paper)"/>
    <text class="dimension-label" transform="translate(1195 240) rotate(90)" text-anchor="middle">1450mm</text>
  </g>

  <rect class="panel-outline" x="2" y="33" width="1168" height="399"/>

  <g clip-path="url(#panel-clip)">
    <g class="service-band" transform="translate(-20 322) rotate(-12)">
      <!-- Row 1 -->
      <text class="service-word" x="0" y="0" font-size="40" textLength="250" lengthAdjust="spacingAndGlyphs">SURROUND SOUND</text>
      <use href="#icon-tile" x="262" y="-30" width="14" height="14"/>
      <text class="service-word" x="280" y="-16" font-size="17" textLength="100" lengthAdjust="spacingAndGlyphs">AUDIO VISUAL</text>
      <text class="service-word service-word--minor" x="262" y="-4" font-size="10" textLength="122" lengthAdjust="spacingAndGlyphs">COMMERCIAL · HOME CINEMA</text>
      <use href="#icon-tile" x="400" y="-30" width="30" height="30"/>
      <text class="service-word" x="438" y="0" font-size="40" textLength="80" lengthAdjust="spacingAndGlyphs">DATA</text>
      <use href="#icon-tile" x="530" y="-30" width="30" height="30"/>
      <text class="service-word" x="568" y="0" font-size="40" textLength="125" lengthAdjust="spacingAndGlyphs">ALARMS</text>

      <!-- Row 2 -->
      <text class="service-word" x="30" y="40" font-size="40" textLength="260" lengthAdjust="spacingAndGlyphs">ACCESS CONTROL</text>
      <text class="service-word service-word--minor" x="302" y="11" font-size="10" textLength="100" lengthAdjust="spacingAndGlyphs">NETWORKING · DOMESTIC</text>
      <use href="#icon-tile" x="302" y="14" width="14" height="14"/>
      <text class="service-word" x="320" y="27" font-size="16" textLength="80" lengthAdjust="spacingAndGlyphs">AUTOMATION</text>
      <text class="service-word service-word--minor" x="302" y="39" font-size="10" textLength="90" lengthAdjust="spacingAndGlyphs">DOMESTIC · CCTV</text>
      <use href="#icon-tile" x="418" y="10" width="30" height="30"/>
      <text class="service-word" x="456" y="40" font-size="40" textLength="195" lengthAdjust="spacingAndGlyphs">AUTOMATION</text>

      <!-- Row 3 -->
      <use href="#icon-tile" x="120" y="52" width="14" height="14"/>
      <text class="service-word" x="138" y="66" font-size="16" textLength="90" lengthAdjust="spacingAndGlyphs">HOME CINEMA</text>
      <text class="service-word service-word--minor" x="120" y="78" font-size="10" textLength="125" lengthAdjust="spacingAndGlyphs">CCTV · AUDIO VISUAL · DATA</text>
      <use href="#icon-tile" x="262" y="50" width="30" height="30"/>
      <text class="service-word" x="300" y="80" font-size="40" textLength="185" lengthAdjust="spacingAndGlyphs">HOME CINEMA</text>
      <text class="service-word service-word--minor" x="497" y="55" font-size="9" textLength="108" lengthAdjust="spacingAndGlyphs">ALARMS · SURROUND SOUND</text>
      <use href="#icon-tile" x="497" y="58" width="11" height="11"/>
      <text class="service-word" x="511" y="69" font-size="13" textLength="26" lengthAdjust="spacingAndGlyphs">CCTV</text>
      <use href="#icon-tile" x="543" y="58" width="11" height="11"/>
      <text class="service-word" x="557" y="69" font-size="13" textLength="48" lengthAdjust="spacingAndGlyphs">DOMESTIC</text>
      <text class="service-word" x="497" y="82" font-size="13" textLength="108" lengthAdjust="spacingAndGlyphs">ACCESS CONTROL</text>
      <use href="#icon-tile" x="615" y="50" width="30" height="30"/>
      <text class="service-word" x="651" y="80" font-size="40" textLength="70" lengthAdjust="spacingAndGlyphs">CCTV</text>

      <!-- Row 4 -->
      <text class="service-word" x="10" y="120" font-size="40" textLength="190" lengthAdjust="spacingAndGlyphs">NETWORKING</text>
      <text class="service-word" x="240" y="120" font-size="40" textLength="125" lengthAdjust="spacingAndGlyphs">ALARMS</text>
      <use href="#icon-tile" x="385" y="94" width="14" height="14"/>
      <text class="service-word" x="403" y="108" font-size="16" textLength="80" lengthAdjust="spacingAndGlyphs">NETWORKING</text>
      <text class="service-word service-word--minor" x="385" y="120" font-size="10" textLength="170" lengthAdjust="spacingAndGlyphs">AUDIO VISUAL · DOMESTIC · NETWORKING</text>
    </g>

    <g class="brand-block">
      <text class="brand-name" transform="translate(712 300) rotate(-12.5)">Kvorin</text>
      <text class="brand-tagline" transform="translate(778 334) rotate(-12.5)">Electrical, Security, AV</text>

      <g class="contact-phone" transform="translate(718 368) rotate(-12.5)">
        <rect class="contact-icon" x="2" y="-24" width="14" height="24" rx="2"/>
        <rect class="contact-icon--solid" x="6" y="-5" width="6" height="2"/>
        <text class="contact-detail" x="24" y="0">0417 265 391</text>
      </g>
      <g class="contact-email" transform="translate(905 330) rotate(-12.5)">
        <rect class="contact-icon--solid" x="0" y="-19" width="30" height="18" rx="3"/>
        <path d="M3 -16 L15 -8 L27 -16" fill="none" stroke="#ffffff" stroke-width="1.8"/>
        <text class="contact-detail" x="38" y="0">sales@kvorin.com.au</text>
      </g>
    </g>
  </g>
</svg>
</body>
</html>
```